Brevard Trade Partners - we are Asian sourcing agents

We are sourcing agents based in the USA and we act as sourcing agents for clients in throughout the world. We focus primarily on custom sewn goods. So basically companies who do not have the in-house expertise to do it themselves, come to us and have us find suitable factories in Asia to do the production. We are middlemen. We find the factories...quote the project...manage the quality control and then deliver the goods directly to our customer's door. We pride ourselves in making the communication very easy and precise.

Current page is www.brevardtradepartners.com

I am not happy w/ the overall look. The spacing...the photos, the fonts...the design elements...the pictures. I want a cool, crisp design that conveys professionalism and clearly depicts/explains what we do.

Requirements
Must have
• use my logo....I like it...it was designed by someone on this website.
Nice to have
• a video/animation of the entire process would be wonderful. Showing initial contact with our office in the USA...then to my correspondence with my offices in Taiwan and in Hong Kong...and then back and fort w/ the customer.....and then between my people in Hong Kong/Taiwan with the local factories......and then a quote is generated and sent to my client......to samples being made and sent for approval.....to a PO being generated......to final samples being sent.....to the order being shipped and delivered to the clients warehouse. I was thinking of an animation showing arrows and text showing the back and forth communication and explaining how the process flows.

```html
<!DOCTYPE html>
<html lang="en">
<head>
<meta charset="utf-8">
<title>Brevard Trade Partners</title>
<link href="https://fonts.googleapis.com/css2?family=Open+Sans:wght@400;600;700;800&display=swap" rel="stylesheet">
<style>
:root{
  --navy:#0f1a5e;
  --green:#5b8a1c;
  --green-light:#7aa43a;
  --text:#555;
  --muted:#888;
  --gray-bg:#ebebeb;
  --footer-dark:#1d1d1d;
  --white:#fff;
}
*{box-sizing:border-box;margin:0;padding:0}
html,body{width:814px;height:1200px;overflow:hidden;background:#fff}
body{font-family:"Open Sans",sans-serif;color:var(--text);position:relative}
.abs{position:absolute}

/* header */
.site-header{position:absolute;left:0;top:0;width:814px;height:73px;background:#fff}
.brand{position:absolute;left:68px;top:22px;display:flex;align-items:center;gap:8px}
.brand-mark{width:16px;height:16px;background:var(--green)}
.brand-name{font-weight:800;font-size:19px;color:var(--navy);letter-spacing:.2px}
.main-nav{position:absolute;right:68px;top:44px;display:flex;gap:23px;font-size:8.5px;text-transform:uppercase;letter-spacing:.3px}
.main-nav a{color:#666;text-decoration:none}
.main-nav a.active{color:var(--green)}

/* hero */
.hero{position:absolute;left:0;top:73px;width:814px;height:308px;overflow:hidden;
  background:
    radial-gradient(ellipse 55% 30% at 50% 26%,rgba(150,162,178,.45) 0%,rgba(150,162,178,0) 100%),
    radial-gradient(ellipse 40% 55% at 50% 78%,rgba(90,92,98,.55) 0%,rgba(90,92,98,0) 100%),
    linear-gradient(180deg,#2d3949 0%,#46546a 35%,#2e333b 62%,#1c1f24 100%)}
.hero-title{position:absolute;top:20px;width:100%;text-align:center;color:#fff;font-size:19px;font-weight:600;text-shadow:0 1px 3px rgba(0,0,0,.5)}
.hero-sub{position:absolute;top:49px;width:100%;text-align:center;color:#fff;font-size:9.5px;font-weight:600;text-shadow:0 1px 2px rgba(0,0,0,.5)}
.hero-arrow{position:absolute;top:143px;width:18px;height:24px;background:rgba(0,0,0,.45)}
.hero-arrow.left{left:0}.hero-arrow.right{right:0}

/* welcome */
.video-box{position:absolute;left:68px;top:418px;width:180px;height:105px;background:linear-gradient(135deg,#3a3a3a,#1c1c1c);box-shadow:4px 4px 0 #ccc}
.video-box .label{position:absolute;top:28px;width:100%;text-align:center;color:#fff;font-weight:700;font-size:14px}
.video-box svg{position:absolute;left:77px;top:52px}
.welcome-title{position:absolute;left:269px;top:412px;font-size:18px;color:var(--green);font-weight:400}
.welcome-text{position:absolute;left:269px;top:442px;width:462px;font-size:7.6px;line-height:14px;color:#666}

/* gray */
.gray{position:absolute;left:0;top:569px;width:814px;height:429px;background:var(--gray-bg)}
.section-title{position:absolute;font-size:18px;color:#555;font-weight:400}
.products-img{position:absolute;left:73px;top:623px;width:208px;height:117px;background:linear-gradient(135deg,#c9c5c0 0%,#b33 55%,#d44 100%)}
.cat-bar{position:absolute;left:73px;width:208px;height:26px;background:var(--navy);color:#fff;font-size:10.5px;padding-left:12px;line-height:26px}
.cat-bar.active{background:linear-gradient(#6f9a2c,var(--green))}
.cat-bar svg{position:absolute;right:10px;top:8px}

.know-box{position:absolute;left:314px;top:598px;width:428px;height:97px;background:#fff}
.know-head{position:absolute;left:16px;top:20px;font-size:17px;font-weight:800;color:#c8c8c8;line-height:22px;letter-spacing:.5px}
.know-list{position:absolute;top:18px;list-style:none;font-size:7.6px;color:#333;line-height:22px}
.know-list li::before{content:"•";margin-right:5px;color:#555}

.news-next{position:absolute;left:728px;top:710px;width:14px;height:14px;background:#bbb}
.news-card{position:absolute;top:735px;width:136px;height:163px;background:#fff}
.news-img{height:81px;background:linear-gradient(135deg,#6b7f9a,#3f4c5f)}
.news-card h3{font-size:7.8px;font-weight:600;color:#222;margin:13px 15px 0;line-height:10.5px}
.news-card p{font-size:6.2px;color:#888;margin:5px 15px 0;line-height:8.5px}

.cta{position:absolute;left:314px;top:913px;width:428px;height:57px;background:#fff}
.cta-avatar{position:absolute;left:8px;top:6px;width:44px;height:44px;border-radius:50%;background:linear-gradient(135deg,#8a7766,#3b3430)}
.cta-title{position:absolute;left:66px;top:12px;font-size:8.8px;font-weight:700;color:#111;line-height:12px}
.cta-text{position:absolute;left:68px;top:38px;font-size:6.2px;color:#888}
.cta-btn{position:absolute;right:8px;top:6px;width:73px;height:44px;background:linear-gradient(#7aa43a,var(--green));color:#fff;font-size:9px;font-weight:700;text-align:center;line-height:12.5px;padding-top:9px}

/* footer */
.footer{position:absolute;left:0;top:998px;width:814px;height:140px;background:#fff}
.f-title{position:absolute;top:22px;font-size:11px;color:#555}
.f-text{position:absolute;font-size:7.3px;color:#666}
.f-links{position:absolute;top:45px;list-style:none;font-size:6.6px;color:#777;line-height:18.7px}
.f-links li::before{content:"•";margin-right:4px}
.f-divider{position:absolute;top:22px;width:1px;height:92px;background:#ddd}
.social{position:absolute;top:46px;width:18px;height:18px;border-radius:50%}
.bottom{position:absolute;left:0;top:1138px;width:814px;height:62px;background:var(--footer-dark)}
.bottom p{position:absolute;left:68px;font-size:6.6px;color:#888}
</style>
</head>
<body>

<header class="site-header">
  <div class="brand"><span class="brand-mark"></span><span class="brand-name">Brevard Trade Partners</span></div>
  <nav class="main-nav">
    <a class="active" href="#">Home</a><a href="#">Product Categories</a><a href="#">About Us</a><a href="#">Request Quote</a>
  </nav>
</header>

<section class="hero" role="img" aria-label="Team of business people in dark suits standing in front of a faint world map">
  <h1 class="hero-title">Asian Outsourcing Made Easy!</h1>
  <p class="hero-sub">Custom Sewn Goods Made to Your Specifications</p>
  <div class="hero-arrow left"><svg width="18" height="24"><path d="M11 6 L6 12 L11 18" stroke="#ccc" fill="none" stroke-width="1.2"/></svg></div>
  <div class="hero-arrow right"><svg width="18" height="24"><path d="M7 6 L12 12 L7 18" stroke="#ccc" fill="none" stroke-width="1.2"/></svg></div>
</section>

<div class="video-box" role="img" aria-label="Video still of a sewing workshop">
  <div class="label">HOW IT WORKS</div>
  <svg width="26" height="26"><circle cx="13" cy="13" r="12" fill="#1e88d0" stroke="#fff" stroke-width="1.5"/><path d="M10 7.5 L18 13 L10 18.5Z" fill="#fff"/></svg>
</div>
<h2 class="welcome-title">Welcome to Brevard</h2>
<p class="welcome-text">Brevard Trade Partners has been sourcing custom sewn goods in Asia since 1998. We work with our clients by matching their unique production needs with the best possible China sewing factories. We manage the entire process from start to finish, by first identifying the best factories to quote each job. The next step is negotiating the best (fair) price possible. We complete the process by monitoring the quality of the goods during production, and then managing the ocean logistics, customs clearances and local delivery right to your door. Our services and our total commitment to customer satisfaction help level the playing field by giving our customers access to low cost, high quality China contract sewing.</p>

<section class="gray">
  <h2 class="section-title" style="left:73px;top:23px">Products</h2>
</section>
<div class="products-img" role="img" aria-label="Hands guiding red fabric through a sewing machine"></div>
<div class="cat-bar active" style="top:740px">Sewn Goods<svg width="10" height="10"><circle cx="5" cy="5" r="5" fill="#fff"/><rect x="2.5" y="4.2" width="5" height="1.6" fill="#5b8a1c"/></svg></div>
<div class="cat-bar" style="top:769px">Bags<svg width="10" height="10"><circle cx="5" cy="5" r="5" fill="#fff"/><rect x="2.5" y="4.2" width="5" height="1.6" fill="#0f1a5e"/></svg></div>
<div class="cat-bar" style="top:804px">Gloves<svg width="10" height="10"><circle cx="5" cy="5" r="5" fill="#fff"/><rect x="2.5" y="4.2" width="5" height="1.6" fill="#0f1a5e"/></svg></div>
<div class="cat-bar" style="top:838px">Covers<svg width="10" height="10"><circle cx="5" cy="5" r="5" fill="#fff"/><rect x="2.5" y="4.2" width="5" height="1.6" fill="#0f1a5e"/></svg></div>
<div class="cat-bar" style="top:873px">Cases<svg width="10" height="10"><circle cx="5" cy="5" r="5" fill="#fff"/><rect x="2.5" y="4.2" width="5" height="1.6" fill="#0f1a5e"/></svg></div>
<div class="cat-bar" style="top:908px">Medical<svg width="10" height="10"><circle cx="5" cy="5" r="5" fill="#fff"/><rect x="2.5" y="4.2" width="5" height="1.6" fill="#0f1a5e"/></svg></div>
<div class="cat-bar" style="top:943px">Sporting Goods<svg width="10" height="10"><circle cx="5" cy="5" r="5" fill="#fff"/><rect x="2.5" y="4.2" width="5" height="1.6" fill="#0f1a5e"/></svg></div>

<div class="know-box">
  <div class="know-head">WHAT YOU<br>NEED TO<br>KNOW</div>
  <ul class="know-list" style="left:137px"><li>Contract Sewing in China</li><li>What is the Process?</li><li>What the Minimum Order?</li></ul>
  <ul class="know-list" style="left:270px"><li>Contract Outsourcing FAQ</li><li>Outsourcing Case Study</li><li>Custom Industrial Sewing in China</li></ul>
</div>

<h2 class="section-title" style="left:314px;top:706px;color:#222">Latest News</h2>
<div class="news-next"><svg width="14" height="14"><path d="M6 4 L9 7 L6 10" stroke="#fff" fill="none" stroke-width="1.2"/></svg></div>

<article class="news-card" style="left:315px">
  <div class="news-img" role="img" aria-label="Factory worker in a hard hat handling bricks" style="background:linear-gradient(135deg,#d9c7b8,#5a6e9a 60%,#b46a4e)"></div>
  <h3>Aenean sed quam non sapien faucibus consequat</h3>
  <p>Proin porta fermentum ipsum, vel porttitor turpis venenatis luctus volutpat eu.</p>
</article>
<article class="news-card" style="left:461px">
  <div class="news-img" role="img" aria-label="Worker at an industrial sewing machine" style="background:linear-gradient(135deg,#8fb6d8,#3c6fa8 60%,#c34aa0)"></div>
  <h3>Aenean sed quam non sapien faucibus consequat</h3>
  <p>Proin porta fermentum ipsum, vel porttitor turpis venenatis luctus volutpat eu.</p>
</article>
<article class="news-card" style="left:606px">
  <div class="news-img" role="img" aria-label="Worker in a metal workshop" style="background:linear-gradient(135deg,#6b6a4e,#3a3a32 60%,#7a6a52)"></div>
  <h3>Aenean sed quam non sapien faucibus consequat</h3>
  <p>Proin porta fermentum ipsum, vel porttitor turpis venenatis luctus volutpat eu.</p>
</article>

<div class="cta">
  <div class="cta-avatar" role="img" aria-label="Portrait of a company representative"></div>
  <div class="cta-title">OUTSOURCE YOUR SEWING NEEDS TO<br>TRUSTED CONTRACTORS IN CHINA</div>
  <div class="cta-text">Please contact us for immediate consultation regarding your outsourcing project.</div>
  <div class="cta-btn">REQUEST<br>QUOTE</div>
</div>

<footer class="footer">
  <div class="f-title" style="left:70px">Support</div>
  <div class="f-text" style="left:72px;top:47px">Tel: 555-014-2290</div>
  <div class="f-text" style="left:72px;top:67px">Fax: 555-014-2291</div>
  <div class="f-text" style="left:72px;top:86px">Email: info@brevardtradepartners.com</div>
  <div class="f-text" style="left:72px;top:105px;font-size:8.5px">Find Locaton</div>
  <div class="f-divider" style="left:207px"></div>
  <div class="f-title" style="left:231px">Quick Links</div>
  <ul class="f-links" style="left:231px"><li>Home</li><li>Product Categories</li><li>About us</li><li>Reques a Quote</li></ul>
  <ul class="f-links" style="left:337px"><li>CUSTOM BAGS</li><li>CUSTOM COVERS</li><li>CUSTOM MEDICAL ACCESSORIES</li><li>CUSTOM SEWN GOODS</li></ul>
  <ul class="f-links" style="left:494px"><li>CUSTOM CASES</li><li>CUSTOM GLOVES</li><li>CUSTOM SPORTING GOODS</li></ul>
  <div class="f-divider" style="left:627px"></div>
  <div class="f-title" style="left:652px">Follow us on</div>
  <div class="social" style="left:652px;background:#2a4e96"></div>
  <div class="social" style="left:675px;background:#1e88d0"></div>
  <div class="social" style="left:698px;background:#333"></div>
  <svg class="social" style="left:721px" width="18" height="18"><circle cx="9" cy="9" r="9" fill="#5b9a2c"/><rect x="4.5" y="5.5" width="9" height="7" fill="none" stroke="#fff" stroke-width="1"/><path d="M4.5 5.5 L9 9.5 L13.5 5.5" fill="none" stroke="#fff" stroke-width="1"/></svg>
</footer>

<div class="bottom">
  <p style="top:22px">Copyright © 2015 Brevard Trade Partners, LLC. All Rights Reserved.</p>
  <p style="top:40px">Disclaimer | Support | Terms andConditions</p>
  <svg class="abs" style="left:701px;top:23px" width="19" height="19"><circle cx="9.5" cy="9.5" r="8.5" fill="none" stroke="#fff" stroke-width="1.2"/><rect x="5" y="6.5" width="9" height="6.5" fill="#fff"/><path d="M5 6.5 L9.5 10 L14 6.5" fill="none" stroke="#1d1d1d" stroke-width="0.9"/></svg>
  <svg class="abs" style="left:725px;top:23px" width="19" height="19"><circle cx="9.5" cy="9.5" r="8.5" fill="none" stroke="#888" stroke-width="1.2"/><path d="M9.5 14 V5.5 M6 9 L9.5 5.5 L13 9" fill="none" stroke="#888" stroke-width="1.3"/></svg>
</div>

</body>
</html>
```